Natural Light/Organic/Documentary Photography Business

I like a simple, approachable, feminine, earthy/organic feel. Earth/neutral tones, nothing too loud or obnoxious. I like the watercolor look. I don't want anything too trendy or something I'll get tired of after a couple months. As far as colors, I am much more a fan of cream/taupe/blue/green...not a fan of pink or purple at all.

Target Market(s)

Weddings & Families

Industry/Entity Type

Wedding Photography

Contact Information for Business Card

website, email, phone number

Font styles to use
Other font styles liked:
• Horizontes, Gotham

Colors

Designer to choose colors to be used in the design.

Requirements
Must have
• Website: www.mirelhatchway.com
• Phone: 418.629.5073
• Email: mirel@mirelhatchway.com
Nice to have
• I like the watercolor look but its not necessary. I like simple/earthy tones. Nothing too loud or distracting. Simple & feminine without being too girly. I like an approachable/soft feel.
• Instagram: www.instagram.com/mirelhatchwayphotography/
Should not have
• NO loud colors or design or pattern. I do not want a photo of a camera or lens or anything cheesy like that.

```html
<!DOCTYPE html>
<html lang="en">
<head>
<meta charset="utf-8">
<title>Mirel Hatchway Photography – Business Card</title>
<link href="https://fonts.googleapis.com/css2?family=Source+Sans+3:wght@400;600&display=swap" rel="stylesheet">
<style>
  :root {
    --backdrop: #ececec;
    --paper: #ffffff;
    --taupe: #8e8077;
    --taupe-text: #877a71;
    --ink: #444444;
    --rule: #9a8f88;
    --edge: #d9d6d3;
  }
  * { margin: 0; padding: 0; box-sizing: border-box; }
  html, body {
    width: 1200px; height: 799px; overflow: hidden;
    background: var(--backdrop);
    font-family: "Source Sans 3", "Myriad Pro", Arial, sans-serif;
  }
  .card {
    position: absolute; left: 313px; width: 584px; height: 333px; overflow: hidden;
  }
  .card-front { top: 51px; background: var(--paper); }
  .card-back { top: 413px; background: var(--taupe); }

  .brand-front {
    position: absolute; right: 44px; top: 58px;
    font-size: 22px; font-weight: 400; color: var(--taupe-text);
    letter-spacing: 0.5px;
  }
  .holder-name {
    position: absolute; left: 38px; top: 179px; line-height: 30px;
    font-size: 21px; font-weight: 600; color: var(--taupe-text);
  }
  .holder-rule {
    position: absolute; left: 37px; right: 47px; top: 213px;
    height: 1px; background: var(--rule);
  }
  .contact-list {
    position: absolute; left: 37px; top: 220px; list-style: none;
  }
  .contact-item {
    display: flex; align-items: center; height: 19px;
    font-size: 15px; color: var(--ink);
  }
  .contact-icon { width: 14px; height: 14px; margin-right: 10px; flex: none; }
  .edge-line {
    position: absolute; left: 0; right: 0; top: 313px; height: 3px; background: var(--edge);
  }
  .edge-band {
    position: absolute; left: 0; right: 0; top: 316px; bottom: 0; background: var(--taupe);
  }

  .brand-back {
    position: absolute; left: 0; right: 0; top: 143px; text-align: center;
    font-size: 34px; line-height: 44px; font-weight: 400; color: var(--paper); letter-spacing: 1px;
  }
  .site-back {
    position: absolute; left: 0; right: 0; top: 276px; text-align: center;
    font-size: 16px; line-height: 22px; font-weight: 400; color: var(--paper); letter-spacing: 3.6px;
  }
</style>
</head>
<body>
  <section class="card card-front">
    <div class="brand-front">Mirel Hatchway Photography</div>
    <div class="holder-name">Mirel Hatchway</div>
    <div class="holder-rule"></div>
    <ul class="contact-list">
      <li class="contact-item">
        <svg class="contact-icon" viewBox="0 0 14 14"><path fill="#877a71" d="M1 5c0-2 2-3 6-3s6 1 6 3v1h-3V5H4v1H1z M3 7h8l1 5H2z"/><circle cx="7" cy="9.5" r="1.5" fill="#fff"/></svg>
        418.629.5073
      </li>
      <li class="contact-item">
        <svg class="contact-icon" viewBox="0 0 14 14"><rect x="0.5" y="3" width="13" height="9" fill="#877a71"/><path d="M0.5 3.5 7 8l6.5-4.5" stroke="#fff" stroke-width="1.2" fill="none"/></svg>
        mirel@mirelhatchway.com
      </li>
      <li class="contact-item">
        <svg class="contact-icon" viewBox="0 0 14 14"><circle cx="7" cy="7" r="6" fill="#877a71"/><path d="M1 7h12M7 1c-3 3-3 9 0 12M7 1c3 3 3 9 0 12" stroke="#fff" stroke-width="1" fill="none"/></svg>
        www.mirelhatchway.com
      </li>
      <li class="contact-item">
        <svg class="contact-icon" viewBox="0 0 14 14"><rect x="1" y="1" width="12" height="12" rx="2" fill="#877a71"/></svg>
        mirelhatchwayphotography
      </li>
    </ul>
    <div class="edge-line"></div>
    <div class="edge-band"></div>
  </section>

  <section class="card card-back">
    <div class="brand-back">Mirel Hatchway Photography</div>
    <div class="site-back">WWW.MIRELHATCHWAY.COM</div>
  </section>
</body>
</html>
```